Sci Fi/ Secret Agent Author needs website design!

My name is Lark Whitby and I am an author. I require a site that can provide information about myself and my books and other works.

I would like it to have a Home, blog function, (about the) books/series section so people can visit another section and read about each individual book that's going to be released. A resources page, a Store, social media links and ability to load/embed videos from clipvane and other.

I write mild scifi/thriller/conspiracy/secret government type novels. -At the moment-. The series follows a strong female lead that is an agent with a secret organisation in a classified military installation.

The theme would be professional yet possibly show this element.

/military fiction/thriller/fantasy/Sci fi/ femme-fatal, readers. Mostly females, age 18-60
Novel readers

5+ page

• Would like designers to follow brief. :)
• My budget includes all the pages I will need;
• eg home, blog, resources, store, ability to pay with coinpouch and Credit Cards
• , ability to have trailers from clipvane etc. Must have links to the social media mentioned in the brief.
• use of the colours I have suggested. electric/indigo purple, fuschia highlights , dark greys
• as I will possibly base branding for social media ETC on the look of your website design and colour scheme.
• Ability for trailer on front page??
• Should not be too cluttered. (But I am open to all ideas)

```html
<!DOCTYPE html>
<html lang="en">
<head>
<meta charset="utf-8">
<title>Lark Whitby — Store</title>
<link rel="stylesheet" href="https://fonts.googleapis.com/css2?family=Roboto+Condensed:wght@400;700&family=Open+Sans:wght@400;600&display=swap">
<style>
:root{
  --purple:#6a0dad;
  --purple-deep:#5a0a99;
  --purple-soft:#7b1fc4;
  --violet-star:#6e12b8;
  --gold:#f0a500;
  --ink:#2b2b2b;
  --text:#555;
  --muted:#777;
  --line:#dcdcdc;
  --panel:#efefef;
  --footer:#f3f3f3;
  --white:#fff;
  --dark-btn:#2a2a2a;
}
*{box-sizing:border-box;margin:0;padding:0}
html,body{width:1200px;height:2169px;overflow:hidden}
body{position:relative;background:var(--white);font-family:"Open Sans",Arial,sans-serif;color:var(--text)}
.heading{font-family:"Roboto Condensed","Arial Narrow",sans-serif}
a{color:inherit;text-decoration:none}

/* Header */
.site-header{position:absolute;left:0;top:0;width:1200px;height:97px;background:var(--purple);display:flex;align-items:center;padding:0 97px}
.brand{font-family:"Roboto Condensed",sans-serif;font-weight:700;font-size:41px;color:var(--white);letter-spacing:.5px}
.main-nav{margin-left:auto;display:flex;gap:31px;align-items:center}
.main-nav a{font-family:"Roboto Condensed",sans-serif;font-size:15px;color:var(--white);text-transform:uppercase}
.nav-social{display:flex;gap:6px;margin-left:0}
.nav-social span{width:10px;height:10px;border-radius:50%;background:var(--white)}

/* Hero */
.hero{position:absolute;left:0;top:97px;width:1200px;height:375px;overflow:hidden}
.hero-photo{position:absolute;inset:0;background:radial-gradient(ellipse 380px 300px at 600px 120px,#8a6a10 0%,#4a3306 45%,#1a0d03 80%),#140a03}
.hero-text{position:absolute;left:0;right:0;top:135px;text-align:center;color:var(--white)}
.hero-title{font-size:43px;font-weight:400;letter-spacing:.5px}
.hero-sub{font-family:"Roboto Condensed",sans-serif;font-size:15px;line-height:26px;margin-top:14px;text-transform:uppercase}
.hero-curve{position:absolute;left:0;bottom:0}

/* Products */
.section-title{position:absolute;left:97px;top:552px;font-size:36px;font-weight:400;color:var(--ink)}
.title-rule{position:absolute;left:97px;top:612px;width:51px;height:2px;background:var(--purple)}
.product-grid{position:absolute;left:97px;top:638px;width:694px;display:grid;grid-template-columns:repeat(3,217px);column-gap:21px;row-gap:39px}
.product-card{height:323px;background:var(--white);border:1px solid var(--line);box-shadow:0 2px 3px rgba(0,0,0,.12);text-align:center}
.product-image{height:211px;margin:0}
.product-name{font-family:"Open Sans",sans-serif;font-size:15px;color:#333;letter-spacing:.5px;margin-top:16px;text-transform:uppercase}
.product-desc{font-size:11px;line-height:17px;color:var(--muted);margin:7px 16px 0}
.stars{color:var(--violet-star);font-size:15px;letter-spacing:2px;margin-top:3px}
.stars .off{color:#999}

/* Sidebar */
.sidebar{position:absolute;left:837px;top:561px;width:264px}
.search{height:44px;border:1px solid #cfcfcf;display:flex;align-items:center;padding:0 16px;font-size:11px;color:#555;text-transform:uppercase}
.search svg{margin-left:auto}
.categories{margin-top:33px}
.cat-head{position:relative;height:43px;width:220px;background:var(--purple);color:var(--white);font-family:"Roboto Condensed",sans-serif;font-size:20px;padding:10px 15px;text-transform:uppercase}
.cat-head::after{content:"";position:absolute;right:-1px;top:0;border-top:43px solid transparent;border-right:40px solid var(--white)}
.cat-list{background:var(--panel);list-style:none;padding:22px 24px 18px;height:188px}
.cat-list li{font-size:12px;color:#555;line-height:31px}

.tabs-box{margin-top:35px;border:1px solid var(--line);height:485px}
.tab-row{display:flex;height:46px}
.tab{flex:1;font-family:"Roboto Condensed",sans-serif;font-size:20px;text-transform:uppercase;display:flex;align-items:center;justify-content:center;color:var(--purple)}
.tab.active{background:var(--purple);color:var(--white)}
.post{display:flex;gap:17px;padding:18px 14px 0 17px;height:146px;border-bottom:1px solid #e4e4e4}
.post:last-child{border-bottom:none}
.post-thumb{width:98px;height:106px;flex:none}
.post-title{font-size:13px;color:#444;margin-top:1px}
.post-stars{color:var(--gold);font-size:10px;letter-spacing:1px;margin-top:4px}
.post-stars .off{color:#bbb}
.post-text{font-size:11px;line-height:17px;color:#666;margin-top:5px}

/* Newsletter */
.newsletter{position:absolute;left:0;top:1476px;width:1200px;height:343px;text-align:center;color:var(--white)}
.newsletter-bg{position:absolute;inset:0;background:linear-gradient(180deg,#7a22c4 0%,#8a2ccd 45%,#9b3fd6 100%)}
.newsletter-inner{position:relative;padding-top:62px}
.newsletter-title{font-size:31px;font-weight:700;text-transform:uppercase}
.newsletter-text{font-size:11.5px;line-height:19px;margin:12px auto 0;width:640px;font-weight:600}
.form-row{display:flex;justify-content:center;gap:11px;margin-top:32px}
.field{width:307px;height:41px;background:var(--white);color:#444;font-size:11px;display:flex;align-items:center;justify-content:center}
.subscribe{display:inline-block;margin-top:27px;width:260px;height:43px;background:var(--dark-btn);color:var(--white);font-family:"Roboto Condensed",sans-serif;font-size:18px;line-height:43px;text-transform:uppercase}

/* Footer */
.site-footer{position:absolute;left:0;top:1819px;width:1200px;height:289px;background:var(--footer)}
.footer-brand{position:absolute;left:97px;top:52px;font-family:"Roboto Condensed",sans-serif;font-weight:700;font-size:40px;color:var(--purple)}
.footer-about{position:absolute;left:97px;top:110px;width:300px;font-size:11.5px;line-height:21px;color:#555}
.footer-col h4{font-family:"Roboto Condensed",sans-serif;font-weight:400;font-size:19px;color:#444;text-transform:uppercase;margin-bottom:22px}
.contact-col{position:absolute;left:473px;top:48px}
.contact-item{display:flex;gap:14px;font-size:12.5px;line-height:20px;color:#555;margin-bottom:11px}
.contact-item svg{flex:none;margin-top:3px}
.links-col{position:absolute;left:787px;top:48px}
.links-col ul{list-style:none}
.links-col li{font-size:11px;color:#555;line-height:20.5px;padding-left:14px;position:relative}
.links-col li::before{content:"";position:absolute;left:0;top:7px;border-left:5px solid #444;border-top:3.5px solid transparent;border-bottom:3.5px solid transparent}
.social-col{position:absolute;left:997px;top:45px}
.social-col ul{list-style:none}
.social-col li{display:flex;align-items:center;gap:10px;font-size:14px;color:#555;margin-bottom:8px}
.social-col .dot{width:25px;height:25px;border:1.5px solid #888;border-radius:50%}
.copyright{position:absolute;left:0;top:2108px;width:1200px;height:61px;border-top:1px solid #ddd;background:var(--white);text-align:center;font-size:11px;color:#555;line-height:59px}
</style>
</head>
<body>

<header class="site-header">
  <div class="brand">LARK WHITBY</div>
  <nav class="main-nav">
    <a href="#">Home</a><a href="#">Books</a><a href="#">Blog</a><a href="#">Resources</a><a href="#">Other Works</a><a href="#">Store</a><a href="#">Contact Us</a>
    <div class="nav-social" aria-label="Social links"><span></span><span></span><span></span><span></span><span></span></div>
  </nav>
</header>

<section class="hero">
  <div class="hero-photo" role="img" aria-label="Moody golden-lit scene of a child gazing at a glowing open book under sparkles and a hot air balloon"></div>
  <div class="hero-text">
    <h1 class="hero-title heading">OUR STORE</h1>
    <p class="hero-sub">I am an author and write mild scifi / secret agent /<br>thriller / conspiracy novels</p>
  </div>
  <svg class="hero-curve" width="1200" height="60" viewBox="0 0 1200 60" aria-hidden="true">
    <path d="M0 0 Q600 80 1200 12 L1200 60 L0 60 Z" fill="#fff"/>
    <path d="M0 0 Q600 80 1200 12" fill="none" stroke="#7b1fc4" stroke-width="6"/>
  </svg>
</section>

<h2 class="section-title heading">LATEST PRODUCTS</h2>
<div class="title-rule"></div>

<main class="product-grid">
  <article class="product-card"><div class="product-image" role="img" aria-label="Open book glowing with blue magical light" style="background:radial-gradient(circle at 50% 45%,#a8d4ff,#3a5aa0 45%,#141a3a)"></div><h3 class="product-name">Conspiracy Novels</h3><p class="product-desc">Sed ut perspiciatis unde omnis iste natus error sit voluptatem</p><div class="stars">★★★★<span class="off">☆</span></div></article>
  <article class="product-card"><div class="product-image" role="img" aria-label="Hands colouring a floral pattern beside sticky notes" style="background:linear-gradient(135deg,#e8d3b0,#d8a88a 50%,#a9c3a0)"></div><h3 class="product-name">Conspiracy Novels</h3><p class="product-desc">Sed ut perspiciatis unde omnis iste natus error sit voluptatem</p><div class="stars">★★★★<span class="off">☆</span></div></article>
  <article class="product-card"><div class="product-image" role="img" aria-label="Fantasy scene of a giant glowing book doorway with balloons and butterflies" style="background:radial-gradient(circle at 55% 55%,#f3c36a,#3d6f7a 55%,#1c2e3a)"></div><h3 class="product-name">Conspiracy Novels</h3><p class="product-desc">Sed ut perspiciatis unde omnis iste natus error sit voluptatem</p><div class="stars">★★★★<span class="off">☆</span></div></article>
  <article class="product-card"><div class="product-image" role="img" aria-label="Lone figure in a misty grey forest" style="background:linear-gradient(180deg,#b9b9b9,#7a7a7a 60%,#4a4a4a)"></div><h3 class="product-name">Conspiracy Novels</h3><p class="product-desc">Sed ut perspiciatis unde omnis iste natus error sit voluptatem</p><div class="stars">★★★★<span class="off">☆</span></div></article>
  <article class="product-card"><div class="product-image" role="img" aria-label="Hands holding an open book in warm light" style="background:radial-gradient(circle at 50% 45%,#fff1d6,#d99a5a 50%,#5a2a14)"></div><h3 class="product-name">Conspiracy Novels</h3><p class="product-desc">Sed ut perspiciatis unde omnis iste natus error sit voluptatem</p><div class="stars">★★★★<span class="off">☆</span></div></article>
  <article class="product-card"><div class="product-image" role="img" aria-label="Monochrome portrait with white feather texture and a blue eye" style="background:linear-gradient(90deg,#cfcfcf,#7a7a7a 55%,#3a3f48)"></div><h3 class="product-name">Conspiracy Novels</h3><p class="product-desc">Sed ut perspiciatis unde omnis iste natus error sit voluptatem</p><div class="stars">★★★★<span class="off">☆</span></div></article>
</main>

<aside class="sidebar">
  <div class="search">Search
    <svg width="11" height="11" viewBox="0 0 12 12" aria-hidden="true"><circle cx="5" cy="5" r="3.8" fill="none" stroke="#333" stroke-width="1.8"/><line x1="7.8" y1="7.8" x2="11" y2="11" stroke="#333" stroke-width="2"/></svg>
  </div>
  <div class="categories">
    <div class="cat-head">Categories</div>
    <ul class="cat-list">
      <li>Sed ut perspiciatis unde omnis</li>
      <li>Excepteur sint occaecat</li>
      <li>Ut enim ad minima veniam</li>
      <li>Neque porro quisquam</li>
      <li>Quis autem vel eum iure</li>
    </ul>
  </div>
  <div class="tabs-box">
    <div class="tab-row"><div class="tab">Recent</div><div class="tab active">Popular</div></div>
    <div class="post"><div class="post-thumb" role="img" aria-label="Dark haunting figure with long hair" style="background:linear-gradient(180deg,#9a9a9a,#3a3a3a)"></div><div><div class="post-title">Nemo enim ipsam</div><div class="post-stars">★★★<span class="off">☆☆</span></div><p class="post-text">Lorem ipsum dolor sit etur adipiscing elit, sed do eiusmod tempor</p></div></div>
    <div class="post"><div class="post-thumb" role="img" aria-label="Figure in a misty forest" style="background:linear-gradient(180deg,#b5b5b5,#555)"></div><div><div class="post-title">Nemo enim ipsam</div><div class="post-stars">★★★<span class="off">☆☆</span></div><p class="post-text">Lorem ipsum dolor sit etur adipiscing elit, sed do eiusmod tempor</p></div></div>
    <div class="post"><div class="post-thumb" role="img" aria-label="Abandoned doll lying on dark gravel" style="background:linear-gradient(180deg,#6a6a6a,#2f2f2f)"></div><div><div class="post-title">Nemo enim ipsam</div><div class="post-stars">★★★<span class="off">☆☆</span></div><p class="post-text">Lorem ipsum dolor sit etur adipiscing elit, sed do eiusmod tempor</p></div></div>
  </div>
</aside>

<section class="newsletter">
  <div class="newsletter-bg" role="img" aria-label="Purple-tinted desert road stretching toward mountains"></div>
  <div class="newsletter-inner">
    <h2 class="newsletter-title heading">Sign up for our newsletter</h2>
    <p class="newsletter-text">Sed ut perspiciatis unde omnis iste natus error sit voluptatem accusantium doloremque laudantium, totam rem aperiam, eaque ipsa quae ab illo inventore veritatis et quasi architecto beatae vitae dicta sunt explicabo</p>
    <div class="form-row"><div class="field">Enter Name</div><div class="field">Enter Email</div></div>
    <div class="subscribe">Subscribe</div>
  </div>
</section>

<footer class="site-footer">
  <div class="footer-brand">LARK WHITBY</div>
  <p class="footer-about">Sed ut perspiciatis unde omnis iste natus error sit voluptatem accusantium doloremque lauantium, totam rem aperiam, eaque ipsa quae ab illo inventore veritatis et quasi architecto beatae vitae dicta sunt explicabo</p>

  <div class="footer-col contact-col">
    <h4>Contact Us</h4>
    <div class="contact-item"><svg width="12" height="15" viewBox="0 0 12 15" aria-hidden="true"><path d="M6 0a6 6 0 0 0-6 6c0 4 6 9 6 9s6-5 6-9a6 6 0 0 0-6-6z" fill="#444"/><circle cx="6" cy="6" r="2.2" fill="#f3f3f3"/></svg><div>Lark Whitby<br>Harbour Lane 14, 40210 Westmoor</div></div>
    <div class="contact-item"><svg width="13" height="13" viewBox="0 0 13 13" aria-hidden="true"><path d="M3 0l2 3-1.4 1.6a8 8 0 0 0 4.8 4.8L10 8l3 2-1 2.5C6 13 0 7 .5 1z" fill="#444"/></svg><div>Phone: +44 20 7946 0321</div></div>
    <div class="contact-item"><svg width="12" height="9" viewBox="0 0 12 9" aria-hidden="true"><rect width="12" height="9" fill="#444"/><path d="M0 0l6 5 6-5" fill="none" stroke="#f3f3f3" stroke-width="1.2"/></svg><div>info@larkwhitby.net</div></div>
  </div>

  <div class="footer-col links-col">
    <h4>Quick Links</h4>
    <ul><li>Home</li><li>About the book</li><li>Blog</li><li>Resources</li><li>Blog</li><li>store</li><li>Contact Us</li></ul>
  </div>

  <div class="footer-col social-col">
    <h4>Social</h4>
    <ul>
      <li><span class="dot"></span>Kinfolk</li>
      <li><span class="dot"></span>Chirper</li>
      <li><span class="dot"></span>Snapframe</li>
      <li><span class="dot"></span>Pinboardly</li>
      <li><span class="dot"></span>clipvane</li>
    </ul>
  </div>
</footer>
<div class="copyright">©2017 Lark Whitby, All Rights Reserved.</div>

</body>
</html>
```